Web design - holistic filmmaker

I need a design for my new website.

I am a holistic filmmaker, ie I make films for healers, alternative practitioners, spiritual people and institutions that offer training in this field.

The design should be noble, bright, convey the feeling of space and expanse and have some particularly beautiful color accents.

The structure is: start page, offer, references, about me, imprint.

As an idea for the start page, I thought that either I could introduce myself as a filmmaker and my offer, or we could start right on the start page with the references, ie photos and links to already realized projects.

If you want more information or an exchange, I'd love to hear from you. At the moment I just don't know how to describe it better.

The winner will then be asked to design a logo.

Target Market(s)

healers, alternative practitioners, spiritual people and institutions that offer training in this field

Industry/Entity Type

Film production

Number of Pages Required

3 page

```html
<!DOCTYPE html>
<html lang="de">
<head>
<meta charset="utf-8">
<title>Lennart – Holistischer Filmemacher</title>
<link href="https://fonts.googleapis.com/css2?family=League+Gothic&family=Raleway:wght@300;400;500;600&display=swap" rel="stylesheet">
<style>
  :root {
    --green: #22b07d;
    --green-bright: #2ec08a;
    --mist: #f3f9f7;
    --white: #ffffff;
    --ink: #111111;
    --text: #333333;
    --hero-dark: #26301f;
    --hero-mid: #5a6a48;
  }
  * { margin: 0; padding: 0; box-sizing: border-box; }
  html, body { width: 1200px; height: 3450px; overflow: hidden; background: var(--white); }
  body { font-family: "Raleway", sans-serif; color: var(--text); }
  .page { position: relative; width: 1200px; height: 3450px; overflow: hidden; background: var(--white); }
  .abs { position: absolute; }

  .display { font-family: "League Gothic", sans-serif; color: var(--ink); font-weight: 400; line-height: 1; }

  /* header */
  .site-header { left: 0; top: 0; width: 1200px; height: 121px; background: var(--white); }
  .brand { left: 113px; top: 30px; font-size: 60px; }
  .main-nav { right: 90px; top: 54px; display: flex; gap: 44px; font-size: 17px; color: #444; }

  /* hero */
  .hero { left: 0; top: 121px; width: 1200px; height: 642px; }
  .hero-photo { position: absolute; inset: 0;
    background: radial-gradient(ellipse at 62% 40%, #a9a39a 0%, #7a7a6a 18%, var(--hero-mid) 38%, var(--hero-dark) 75%); }
  .hero-title-small { left: 113px; top: 285px; font-size: 60px; color: var(--white); }
  .hero-rule { left: 113px; top: 352px; width: 196px; height: 4px; background: var(--white); }
  .hero-title-big { left: 113px; top: 365px; font-size: 96px; color: var(--white); }
  .btn { display: block; background: var(--green); color: var(--white); font-size: 17px; text-align: center; line-height: 42px; height: 42px; width: 146px; }
  .hero-btn { left: 113px; top: 471px; }

  /* sections */
  .about-band { left: 0; top: 686px; width: 1200px; height: 754px; background: var(--mist); }
  .offer-band { position: absolute; left: 0; top: 2163px; width: 1200px; height: 900px; background: var(--mist); }
  .section-title { font-size: 50px; }
  .body-copy { font-size: 16.4px; line-height: 29.2px; text-align: justify; color: var(--text); font-weight: 300; }

  .video-frame { border: 10px solid var(--green); border-top-width: 8px; border-bottom-width: 12px; border-radius: 46px; overflow: hidden; }
  .video-frame .thumb, .slide { position: absolute; inset: 0; }
  .play { position: absolute; left: 50%; top: 50%; transform: translate(-50%, -50%); border-radius: 50%; border: 3px solid rgba(255,255,255,.9); background: rgba(255,255,255,.18); }
  .play svg { position: absolute; left: 50%; top: 50%; transform: translate(-40%, -50%); }

  /* carousel */
  .slide-frame { top: 1663px; height: 500px; overflow: hidden; }
  .arrow { width: 55px; height: 43px; background: var(--green); display: flex; align-items: center; justify-content: center; }

  /* footer */
  .footer-logo { left: 113px; top: 3150px; font-size: 58px; }
  .footer-about { left: 113px; top: 3236px; width: 232px; font-size: 14.5px; line-height: 29px; text-align: justify; color: #444; }
  .footer-col h4 { font-size: 17px; font-weight: 600; color: var(--ink); margin-bottom: 12px; }
  .footer-col li { list-style: none; font-size: 15px; line-height: 29.5px; color: #444; }
  .newsletter { left: 832px; top: 3197px; width: 256px; height: 39px; background: #eef1f0; display: flex; align-items: center; justify-content: space-between; padding: 0 14px 0 18px; font-size: 15px; color: #999; }
  .social { top: 3266px; width: 31px; height: 31px; border-radius: 50%; }
  .copyright-bar { left: 0; top: 3382px; width: 1200px; height: 68px; background: var(--green-bright); color: var(--white); font-size: 17px; text-align: center; line-height: 68px; font-weight: 300; }
</style>
</head>
<body>
<div class="page">

  <header class="site-header abs">
    <div class="brand display abs">Lennart</div>
    <nav class="main-nav abs">
      <span>Home</span><span>My Offer</span><span>References</span><span>About Me</span><span>Imprint</span>
    </nav>
  </header>

  <section class="hero abs">
    <div class="hero-photo" role="img" aria-label="Portrait of the filmmaker outdoors against a blurred green background"></div>
  </section>
  <div class="hero-title-small display abs">Willkommen Zu</div>
  <div class="hero-rule abs"></div>
  <div class="hero-title-big display abs">Lennart</div>
  <a class="btn hero-btn abs">Loslegen</a>

  <div class="about-band abs"></div>
  <svg class="abs" style="left:0;top:630px" width="1200" height="140" viewBox="0 0 1200 140">
    <polygon points="0,0 0,140 1200,140 1200,130 0,56" fill="#f3f9f7"/>
    <polygon points="0,6 1200,128 1200,132 0,56" fill="#22b07d"/>
  </svg>

  <h2 class="section-title display abs" style="left:112px;top:948px">Über Mich</h2>
  <p class="body-copy abs" style="left:113px;top:1034px;width:488px">Mein Name ist Lennart und ich mache Filme - mit Begeisterung und von ganzem Herzen. Ich bin ein holistischer Filmemacher. Ende der 1990er Jahre stand ich vor der Frage, ob ich beruflich in die Alternativmedizin oder in die Filmbranche gehen solle. Beruflich habe ich mich damals für den Film entschieden, aber das Geistig-Spirituelle und meine Leidenschaft für die sogenannten alternativen Heilmethoden begleiten mich seitdem fast genauso intensiv.</p>
  <a class="btn abs" style="left:113px;top:1307px">Weiterlesen</a>

  <div class="video-frame abs" style="left:645px;top:981px;width:443px;height:312px">
    <div class="thumb" role="img" aria-label="Video still of a woman under a blue sky with a tower behind" style="background:linear-gradient(160deg,#5f86b6 0%,#8fb0d2 45%,#6a5a4c 75%,#3b3028 100%)"></div>
    <div class="play" style="width:84px;height:84px"><svg width="28" height="32" viewBox="0 0 30 34"><polygon points="0,0 30,17 0,34" fill="#ffffff"/></svg></div>
  </div>

  <h2 class="section-title display abs" style="left:0;width:1200px;text-align:center;top:1548px">Projekte</h2>

  <div class="slide-frame abs" style="left:0;width:114px">
    <div class="slide" role="img" aria-label="Project still with a city tower against blue sky" style="background:linear-gradient(100deg,#6f8fb6,#c9c4b8 60%,#8a8070)"></div>
  </div>
  <div class="slide-frame abs" style="left:159px;width:882px">
    <div class="slide" role="img" aria-label="Project still of two practitioners giving a treatment to a resting client" style="background:radial-gradient(ellipse at 55% 55%,#9a7062 0%,#6c5a4c 35%,#4a4a38 70%,#3a3d30 100%)"></div>
    <div class="play" style="width:130px;height:130px"><svg width="44" height="50" viewBox="0 0 30 34"><polygon points="0,0 30,17 0,34" fill="#ffffff"/></svg></div>
  </div>
  <div class="slide-frame abs" style="left:1086px;width:114px">
    <div class="slide" role="img" aria-label="Project still outdoors among green trees" style="background:linear-gradient(90deg,#6f7a4e,#9aa27a)"></div>
  </div>

  <div class="offer-band"></div>
  <div class="arrow abs" style="left:536px;top:2228px"><svg width="16" height="22" viewBox="0 0 16 22"><polyline points="12,3 4,11 12,19" fill="none" stroke="#fff" stroke-width="3"/></svg></div>
  <div class="arrow abs" style="left:610px;top:2228px"><svg width="16" height="22" viewBox="0 0 16 22"><polyline points="4,3 12,11 4,19" fill="none" stroke="#fff" stroke-width="3"/></svg></div>

  <h2 class="section-title display abs" style="left:600px;top:2391px">Angebot</h2>
  <div class="video-frame abs" style="left:119px;top:2460px;width:443px;height:310px">
    <div class="thumb" role="img" aria-label="Video still of a woman in a pink sweater presenting in front of a flip chart" style="background:linear-gradient(90deg,#6a5048 0%,#d9d2c6 25%,#c9a98e 50%,#b04a76 62%,#d8c4a8 85%,#b48a5a 100%)"></div>
    <div class="play" style="width:80px;height:80px"><svg width="26" height="30" viewBox="0 0 30 34"><polygon points="0,0 30,17 0,34" fill="#ffffff"/></svg></div>
  </div>
  <p class="body-copy abs" style="left:600px;top:2478px;width:488px">Einen Film zu drehen ist immer auch eine Reise zu sich selbst. Mit einfachen Mitteln und ohne Spezialeffekte begleite ich Sie auf dem Weg, Ihr Wesen darzustellen. Ein dokumentarischer Werbefilm nah am Menschen. Bilder der Stille richtet sich an alle Menschen und Institutionen, deren Streben nach Wahrhaftigkeit die Triebfeder ihres Handelns ist. Hochwertige Bildgestaltung und die informative und verständliche Vermittlung komplexer Sachverhalte sind Leidenschaft und Grundlage meiner Imagefilme und Unternehmenspräsentationen.</p>
  <a class="btn abs" style="left:598px;top:2808px">Weiterlesen</a>

  <svg class="abs" style="left:0;top:2975px" width="1200" height="140" viewBox="0 0 1200 140">
    <polygon points="0,0 1200,80 1200,140 0,140" fill="#ffffff"/>
    <polygon points="0,8 1200,82 1200,132" fill="#22b07d"/>
  </svg>

  <div class="footer-logo display abs">Lennart</div>
  <p class="footer-about abs">Lorem ipsum dolor sit amet, consectetur adipiscing elit, sed do t dolore magna aliqua.</p>
  <div class="footer-col abs" style="left:451px;top:3160px">
    <h4>Quick Links</h4>
    <ul><li>Home</li><li>My Offer</li><li>References</li><li>About Me</li><li>Imprint</li></ul>
  </div>
  <div class="footer-col abs" style="left:634px;top:3160px">
    <h4>Help Links</h4>
    <ul><li>Support</li><li>Terms &amp; Conditions</li><li>Privacy Policy</li><li>FAQ</li></ul>
  </div>
  <div class="footer-col abs" style="left:832px;top:3160px"><h4>Stay Connected</h4></div>
  <div class="newsletter abs"><span>Email</span>
    <svg width="14" height="12" viewBox="0 0 14 12"><polygon points="0,0 14,6 0,12 3,6" fill="#22b07d"/></svg>
  </div>
  <div class="social abs" style="left:832px;background:#1d9bf0"></div>
  <div class="social abs" style="left:875px;background:#3b5998"></div>
  <div class="social abs" style="left:919px;background:#d6249f"></div>
  <div class="social abs" style="left:962px;background:#0a66c2"></div>

  <div class="copyright-bar abs">© Copyrights 2023 Lennart | All Rights Reserved</div>
</div>
</body>
</html>
```